VAN WRAP

Half wrap Design for a Standard White Kalvento 2023 Tolvari Van (High ROOF)
We are an AIR CONDITIONING, HEATING AND DUCT CLEANING COMPANY
I included pictures of some designs we like for your reference..

Industry/Entity Type

HVAC

Colors

Designer to choose colors to be used in the design.

Requirements
Nice to have
• Phone number: 555-014-3926 ... Services we offer: Air Conditioning- Heating- Duct cleaning
Should not have
• Not too busy

```html
<!DOCTYPE html>
<html lang="en">
<head>
<meta charset="utf-8">
<title>The Climate Crew HVAC Services – Van Side Wrap</title>
<link rel="stylesheet" href="https://fonts.googleapis.com/css2?family=Montserrat:wght@700;800&family=Roboto+Condensed:wght@700&display=swap">
<style>
  :root {
    --ink: #0b0b0b;
    --paper: #ffffff;
    --emblem-fill: #e4e4e4;
  }
  * { margin: 0; padding: 0; box-sizing: border-box; }
  html, body { width: 1200px; height: 759px; overflow: hidden; background: var(--paper); }
  .wrap-panel {
    position: relative;
    width: 1200px;
    height: 759px;
    background: var(--paper);
    color: var(--ink);
  }
  .emblem {
    position: absolute;
    left: 92px;
    top: 180px;
    width: 392px;
    height: 392px;
    border-radius: 50%;
    border: 9px solid var(--ink);
    background: radial-gradient(circle at 50% 42%, #f0f0f0, var(--emblem-fill));
    z-index: 2;
  }
  .brand-name {
    position: absolute;
    left: 522px;
    top: 220px;
    width: 506px;
    font-family: "Montserrat", sans-serif;
    font-weight: 800;
    color: var(--ink);
    line-height: 1;
  }
  .brand-top, .brand-bottom {
    display: flex;
    align-items: center;
    gap: 10px;
  }
  .brand-the { font-size: 26px; letter-spacing: 4px; }
  .brand-rule { height: 7px; background: var(--ink); }
  .brand-top .brand-rule { flex: 1; }
  .brand-main {
    display: block;
    font-size: 51px;
    letter-spacing: 0.5px;
    margin: 6px 0 4px;
    white-space: nowrap;
  }
  .brand-bottom .brand-rule { width: 150px; }
  .brand-sub {
    margin-left: auto;
    font-size: 25px;
    font-weight: 700;
    letter-spacing: 4px;
  }
  .phone-band {
    position: absolute;
    left: 474px;
    top: 378px;
    width: 634px;
    height: 84px;
    background: var(--ink);
    display: flex;
    align-items: center;
    justify-content: center;
    gap: 18px;
    padding-left: 40px;
    color: var(--paper);
    font-family: "Montserrat", sans-serif;
    font-weight: 700;
    font-size: 40px;
    letter-spacing: 1px;
    z-index: 1;
  }
  .phone-band svg { width: 38px; height: 38px; }
  .service-list {
    position: absolute;
    left: 560px;
    top: 472px;
    width: 460px;
    font-family: "Roboto Condensed", sans-serif;
    font-weight: 700;
    font-size: 25px;
    color: var(--ink);
    display: flex;
    justify-content: space-between;
    white-space: nowrap;
  }
</style>
</head>
<body>
  <main class="wrap-panel">
    <div class="emblem" role="img" aria-label="Illustration of an HVAC technician in a cap holding an adjustable wrench"></div>

    <div class="brand-name">
      <div class="brand-top">
        <span class="brand-the">THE</span>
        <span class="brand-rule"></span>
      </div>
      <span class="brand-main">CLIMATE CREW</span>
      <div class="brand-bottom">
        <span class="brand-rule"></span>
        <span class="brand-sub">HVAC SERVICES</span>
      </div>
    </div>

    <div class="phone-band">
      <svg viewBox="0 0 24 24" aria-hidden="true">
        <path fill="#fff" d="M6.6 10.8a15.1 15.1 0 0 0 6.6 6.6l2.2-2.2a1 1 0 0 1 1-.25 11.4 11.4 0 0 0 3.6.57 1 1 0 0 1 1 1V20a1 1 0 0 1-1 1A17 17 0 0 1 3 4a1 1 0 0 1 1-1h3.5a1 1 0 0 1 1 1c0 1.25.2 2.45.57 3.57a1 1 0 0 1-.25 1z"/>
        <path fill="none" stroke="#fff" stroke-width="1.6" stroke-linecap="round" d="M14.5 3.5a6 6 0 0 1 6 6M14.5 6.8a2.8 2.8 0 0 1 2.8 2.8"/>
      </svg>
      <span class="phone-number">555-014-3926</span>
    </div>

    <div class="service-list">
      <span>Air Conditioning</span><span>•</span><span>Heating</span><span>•</span><span>Duct cleaning</span>
    </div>
  </main>
</body>
</html>
```